High-End Print/Digital Ad for Unique Luxury Travel Company Required

Objective:
Design a compelling and visually striking advertisement that highlights our company’s unmatched luxury travel experiences. The ad should elevate our brand image, spark curiosity, and drive prospective clients to contact us.
Target Audience:
• Affluent individuals seeking extraordinary, tailor-made travel experiences
• Affluent, luxury, high-net-worth individuals looking for value, expertise, and white-glove service
• Professionals or retirees who appreciate unique, thoughtfully curated travel over mainstream tourism
Key Messages to Communicate:
• One-of-a-kind luxury travel: Once-in-a-lifetime experiences that are curated with creativity and meticulous attention to detail
• Exceptional service: White-glove, personalized planning from start to finish
• 38 years’ travel experience – expert knowledge of destinations, modes of travel, premium accommodations and well-established, meaningful industry connections.
• Highly trusted: Cruise line executives often say, “No one does what you do.”
Tone and Style:
• Elegant, luxurious, sophisticated
• Eye-catching, polished, and modern
• Professional but warm—conveys trust and credibility
• High-impact visuals (full-bleed imagery, custom graphics, or high-end photography)
Deliverables:
• One full-page print ad and digital ad
• Ready-to-print, high-resolution file + working file (PSD, AI, etc.)
Optional: Social media-optimized version or short motion-graphic variation (if designer offers it)
Inspiration & Visual Style Suggestions:
• Think Lumen Voyages, Harrow Pike Wanderer, Silver Quill, or Orvel Retreats ad styles
• Large, emotive imagery with elegant typography
• Clean layout that speaks luxury, clarity, and trust
Copy Direction (draft):
For those who’ve explored the world—and crave something beyond the ordinary.
Each journey is a masterfully curated experience, rich in detail, seamless in execution, and unforgettable in every way.
Founded in 1997, Tidewell Journeys is a unique travel company specializing in cruising, all-inclusive luxury properties, and tours world-wide for individuals, groups, and incentives.
We offer an exceptional range of services designed to ensure every journey is flawlessly executed and truly unforgettable.
Let us help you plan your next extraordinary adventure.
Note: You may refine the copy slightly based on layout or format needs.
Other Resources for References:
1. Website - www.tidewelljourneys-example.com

```html
<!DOCTYPE html>
<html lang="en">
<head>
<meta charset="utf-8">
<title>Tidewell Journeys — Print and Social Ad</title>
<link rel="stylesheet" href="https://fonts.googleapis.com/css2?family=Playfair+Display:wght@700&family=Raleway:wght@300;400;600;700&family=Montserrat:wght@700&display=swap">
<style>
  :root{
    --board:#a7a8ab;
    --royal:#2a56a6;
    --navy:#1b3a78;
    --band:#1f3f7c;
    --gold:#f7b614;
    --gold-text:#f8c32a;
    --magenta:#b0338f;
    --magenta-dark:#8f2474;
    --white:#ffffff;
    --ink:#1a1d2b;
    --url-blue:#1d4494;
  }
  *{box-sizing:border-box;margin:0;padding:0}
  html,body{width:1200px;height:3105px;overflow:hidden}
  body{background:var(--board);position:relative;font-family:"Raleway",sans-serif}

  .ad{position:absolute;left:279px;width:642px;overflow:hidden;color:var(--white);
      box-shadow:0 24px 40px rgba(0,0,0,.28)}
  .ad--portrait{height:909px}
  .ad--square{height:642px}
  .ad--hero{top:110px}
  .ad--flat{top:1229px}
  .ad--social{top:2295px}

  .ad__scene{position:absolute;left:0;top:0;width:100%;
      background:
        radial-gradient(ellipse 60% 30% at 45% 62%,rgba(255,196,90,.55),rgba(255,196,90,0) 70%),
        radial-gradient(ellipse 55% 40% at 60% 55%,rgba(226,228,240,.85),rgba(226,228,240,0) 75%),
        linear-gradient(180deg,#2450a3 0%,#3563b2 20%,#7d9bd0 38%,#a9b6d8 50%,#8c93b8 62%,#4e5f94 78%,#26407f 100%)}
  .ad--portrait .ad__scene{height:600px}
  .ad--square .ad__scene{height:570px}
  .ad__base{position:absolute;left:0;right:0;background:var(--royal)}
  .ad--portrait .ad__base{top:590px;bottom:0}

  .ad__brand{position:absolute;top:0;background:var(--white);display:flex;align-items:center;justify-content:center;gap:8px;
      color:var(--navy);font-family:"Playfair Display",serif;font-weight:700}
  .ad--portrait .ad__brand{left:194px;width:254px;height:70px;font-size:21px}
  .ad--square .ad__brand{left:217px;width:207px;height:54px;font-size:17px}
  .ad__brand-dot{width:12px;height:12px;border-radius:50%;background:var(--navy)}

  .ad__headline{position:absolute;left:0;right:0;top:0;height:0;text-align:center;font-family:"Playfair Display",serif;font-weight:700}
  .ad__headline-line{position:absolute;left:0;right:0;display:block;white-space:nowrap}
  .ad--portrait .ad__headline{font-size:43px}
  .ad--portrait .ad__headline-line{height:50px;line-height:50px}
  .ad--portrait .ad__headline-line--first{top:97px}
  .ad--portrait .ad__headline-line--second{top:145px}
  .ad--square .ad__headline{font-size:37px}
  .ad--square .ad__headline-line{height:44px;line-height:44px}
  .ad--square .ad__headline-line--first{top:74px}
  .ad--square .ad__headline-line--second{top:124px}
  .ad__world{font-family:"Raleway",sans-serif;font-weight:300;color:var(--gold-text);letter-spacing:-1px;line-height:0}
  .ad--portrait .ad__world{font-size:90px}
  .ad--square .ad__world{font-size:76px}

  .ad__tagline{position:absolute;background:var(--band);text-align:center;font-weight:400;white-space:nowrap}
  .ad--portrait .ad__tagline{left:80px;width:481px;top:202px;height:34px;line-height:34px;font-size:22px}
  .ad--square .ad__tagline{left:94px;width:460px;top:174px;height:31px;line-height:31px;font-size:21px}

  .ad__seal{position:absolute;border-radius:50%;background:radial-gradient(circle at 40% 35%,var(--magenta) 60%,var(--magenta-dark));
      border:6px solid rgba(255,255,255,.85);display:flex;align-items:center;justify-content:center;text-align:center;
      font-family:"Playfair Display",serif;font-weight:700;line-height:1.12;box-shadow:0 6px 14px rgba(0,0,0,.3);z-index:2}
  .ad--portrait .ad__seal{left:34px;top:583px;width:248px;height:248px;font-size:20px}
  .ad--square .ad__seal{left:79px;top:430px;width:144px;height:144px;font-size:11px;border-width:4px}

  .ad__about{position:absolute;left:308px;top:647px;width:316px;font-size:10.3px;line-height:1.3;font-weight:400}
  .ad__about p + p{margin-top:9px}
  .ad__about strong{font-weight:700}

  .ad__gallery{position:absolute;left:308px;top:743px;width:310px;height:102px;z-index:1;
      background:linear-gradient(90deg,#4a8fc9 0%,#c99b3c 35%,#8a6a2e 55%,#e6b259 80%,#f2c57a 100%)}

  .ad__footer{position:absolute;left:0;right:0;bottom:0;background:var(--white)}
  .ad--portrait .ad__footer{height:99px}
  .ad--square .ad__footer{height:80px}
  .ad__invite{position:absolute;color:var(--ink);font-weight:700;line-height:1.25}
  .ad--portrait .ad__invite{left:41px;top:37px;font-size:17.5px}
  .ad--square .ad__invite{left:36px;top:18px;font-size:17px}

  .ad__contact{position:absolute;background:var(--gold);color:var(--url-blue);text-align:center;white-space:nowrap}
  .ad--portrait .ad__contact{left:308px;width:310px;top:33px;bottom:0;padding-top:12px}
  .ad--square .ad__contact{left:311px;right:0;top:10px;bottom:0;padding:16px 0 0 20px;
      clip-path:polygon(18px 0,100% 0,100% 100%,0 100%)}
  .ad__url{font-family:"Montserrat",sans-serif;font-weight:700;font-size:13px;letter-spacing:-.3px}
  .ad__details{font-size:9.6px;margin-top:6px;color:var(--ink)}

  .board-label{position:absolute;left:0;right:0;top:2222px;text-align:center;font-size:19px;letter-spacing:4px;color:#2b2b2e;font-weight:400}
</style>
</head>
<body>

<!-- Print ad, featured -->
<section class="ad ad--portrait ad--hero">
  <div class="ad__scene" role="img" aria-label="Photograph of a lit luxury cruise ship docked at dusk under a blue sky"></div>
  <div class="ad__base"></div>
  <div class="ad__brand"><span class="ad__brand-dot"></span>Tidewell Journeys</div>
  <h1 class="ad__headline"><span class="ad__headline-line ad__headline-line--first">For those who’ve</span><span class="ad__headline-line ad__headline-line--second">explored the <span class="ad__world">world</span></span></h1>
  <p class="ad__tagline">and crave something beyond the ordinary.</p>
  <div class="ad__seal"><p>Each journey<br>is a masterfully<br>curated experience,<br>rich in detail,<br>seamless in execution,<br>and unforgettable<br>in every way.</p></div>
  <div class="ad__about">
    <p>Founded in 1997, Tidewell Journeys is a unique travel company specializing in cruising, all-inclusive luxury properties, and tours world-wide for individuals, groups, and incentives.</p>
    <p><strong>We offer</strong> an exceptional range of services designed to ensure every journey is flawlessly executed and truly unforgettable.</p>
  </div>
  <div class="ad__gallery" role="img" aria-label="Travel photographs: sailboat on a river, ancient stone statues and desert pyramids at sunset"></div>
  <div class="ad__footer">
    <p class="ad__invite">Let us help you plan your<br>next extraordinary adventure.</p>
    <div class="ad__contact">
      <p class="ad__url">WWW.TIDEWELLJOURNEYS-EXAMPLE.COM</p>
      <p class="ad__details">877.555.0142 | travelplans@tidewelljourneys-example.com</p>
    </div>
  </div>
</section>

<!-- Print ad, flat -->
<section class="ad ad--portrait ad--flat">
  <div class="ad__scene" role="img" aria-label="Photograph of a lit luxury cruise ship docked at dusk under a blue sky"></div>
  <div class="ad__base"></div>
  <div class="ad__brand"><span class="ad__brand-dot"></span>Tidewell Journeys</div>
  <h2 class="ad__headline"><span class="ad__headline-line ad__headline-line--first">For those who’ve</span><span class="ad__headline-line ad__headline-line--second">explored the <span class="ad__world">world</span></span></h2>
  <p class="ad__tagline">and crave something beyond the ordinary.</p>
  <div class="ad__seal"><p>Each journey<br>is a masterfully<br>curated experience,<br>rich in detail,<br>seamless in execution,<br>and unforgettable<br>in every way.</p></div>
  <div class="ad__about">
    <p>Founded in 1997, Tidewell Journeys is a unique travel company specializing in cruising, all-inclusive luxury properties, and tours world-wide for individuals, groups, and incentives.</p>
    <p><strong>We offer</strong> an exceptional range of services designed to ensure every journey is flawlessly executed and truly unforgettable.</p>
  </div>
  <div class="ad__gallery" role="img" aria-label="Travel photographs: sailboat on a river, ancient stone statues and desert pyramids at sunset"></div>
  <div class="ad__footer">
    <p class="ad__invite">Let us help you plan your<br>next extraordinary adventure.</p>
    <div class="ad__contact">
      <p class="ad__url">WWW.TIDEWELLJOURNEYS-EXAMPLE.COM</p>
      <p class="ad__details">877.555.0142 | travelplans@tidewelljourneys-example.com</p>
    </div>
  </div>
</section>

<p class="board-label">Social Media</p>

<!-- Social media square -->
<section class="ad ad--square ad--social">
  <div class="ad__scene" role="img" aria-label="Photograph of a lit luxury cruise ship docked at dusk under a blue sky"></div>
  <div class="ad__brand"><span class="ad__brand-dot"></span>Tidewell Journeys</div>
  <h2 class="ad__headline"><span class="ad__headline-line ad__headline-line--first">For those who’ve</span><span class="ad__headline-line ad__headline-line--second">explored the <span class="ad__world">world</span></span></h2>
  <p class="ad__tagline">and crave something beyond the ordinary.</p>
  <div class="ad__seal"><p>Each journey<br>is a masterfully<br>curated experience,<br>rich in detail,<br>seamless in execution,<br>and unforgettable<br>in every way.</p></div>
  <div class="ad__footer">
    <p class="ad__invite">Let us help you plan your<br>next extraordinary adventure.</p>
    <div class="ad__contact">
      <p class="ad__url">WWW.TIDEWELLJOURNEYS-EXAMPLE.COM</p>
      <p class="ad__details">877.555.0142 | travelplans@tidewelljourneys-example.com</p>
    </div>
  </div>
</section>

</body>
</html>
```